Real Estate Business Card

On the front side I want to have my info, my brokerage info.
On the back side I want have my complany’s logo, website and Facebook link. I will provide all this once I select a design.

I would like to see Black background and gold text, Dark Blue and gold text and White and blue text designs

Font styles to use
Sans Serif
Script

```html
<!DOCTYPE html>
<html lang="en">
<head>
<meta charset="utf-8">
<title>Harborline Realty – Business Card</title>
<link href="https://fonts.googleapis.com/css2?family=Cinzel:wght@600&family=Open+Sans:wght@400&display=swap" rel="stylesheet">
<style>
  :root {
    --surface: #2a2a2a;
    --card-top: #1c1c1c;
    --card-bottom: #050505;
    --gold: #e6c22a;
    --gold-deep: #c99a12;
    --text-light: #e4e4e4;
    --text-muted: #bdbdbd;
    --divider: #3a3a3a;
  }
  * { box-sizing: border-box; margin: 0; padding: 0; }
  html, body {
    width: 1200px; height: 900px; overflow: hidden;
    background: var(--surface);
  }
  .canvas {
    width: 1200px; height: 900px;
    display: flex; flex-direction: column; align-items: center; justify-content: center;
    gap: 44px;
  }
  .card {
    position: relative;
    width: 600px; height: 343px;
    background: linear-gradient(160deg, var(--card-top), var(--card-bottom));
    box-shadow: 0 10px 24px rgba(0,0,0,.45);
    overflow: hidden;
  }
  .card__band {
    position: absolute; left: 0; right: 0; bottom: 0; height: 11px;
    background: linear-gradient(180deg, var(--gold), var(--gold-deep));
  }

  /* Logo side */
  .brand {
    position: absolute; left: 0; right: 0; top: 118px;
    text-align: center;
    font-family: "Cinzel", serif; font-weight: 600;
    font-size: 40px; letter-spacing: 1px;
    color: var(--gold);
  }
  .social-link {
    position: absolute; left: 0; right: 0; top: 214px;
    text-align: center;
    font-family: "Open Sans", sans-serif; font-size: 17px;
    color: var(--text-light);
  }

  /* Info side */
  .person {
    position: absolute; left: 70px; top: 104px; width: 230px;
    text-align: right;
  }
  .person__name {
    font-family: "Cinzel", serif; font-weight: 600;
    font-size: 24px; color: var(--gold); letter-spacing: .5px;
  }
  .person__title {
    font-family: "Open Sans", sans-serif; font-size: 15px;
    color: var(--text-muted); margin-top: 0;
  }
  .divider {
    position: absolute; left: 318px; top: 96px; width: 1px; height: 100px;
    background: var(--divider);
  }
  .contact-list {
    position: absolute; left: 340px; top: 100px;
    list-style: none;
    font-family: "Open Sans", sans-serif; font-size: 15px; line-height: 19px;
    color: var(--text-light);
  }
  .contact-list li { display: flex; align-items: center; gap: 8px; }
  .contact-list svg { width: 12px; height: 12px; fill: var(--gold); flex: none; }
  .address {
    position: absolute; left: 84px; top: 256px;
    font-family: "Open Sans", sans-serif; font-size: 15px;
    color: var(--text-light);
  }
</style>
</head>
<body>
<main class="canvas">
  <section class="card card--logo-side">
    <h1 class="brand">Harborline Realty</h1>
    <p class="social-link">social.harborlinerealty.com</p>
    <div class="card__band"></div>
  </section>

  <section class="card card--info-side">
    <div class="person">
      <h2 class="person__name">Marcus Hale</h2>
      <p class="person__title">Managing Director</p>
    </div>
    <div class="divider"></div>
    <ul class="contact-list">
      <li><svg viewBox="0 0 12 12"><path d="M1 4c0-2 1-3 5-3s5 1 5 3l-2 1-1-1.5H4L3 5 1 4zM3 6h6l1 5H2z"/></svg>044-555 210 118</li>
      <li><svg viewBox="0 0 12 12"><path d="M3 0h6v12H3zM4 1.5v8h4v-8z"/></svg>044-555 210 119</li>
      <li><svg viewBox="0 0 12 12"><path d="M3 0h6v3H3zM0 4h12v5h-2V7H2v2H0zM3 8h6v4H3z"/></svg>044-555 210 120</li>
      <li><svg viewBox="0 0 12 12"><path d="M0 2h12v8H0zM1 3l5 4 5-4z" fill-rule="evenodd"/></svg>hello@harborlinerealty.com</li>
      <li><svg viewBox="0 0 12 12"><circle cx="6" cy="6" r="6"/></svg>www.harborlinerealty.com</li>
    </ul>
    <p class="address">48, Quayside Lane Port Ellery Westmarch, 204816.</p>
    <div class="card__band"></div>
  </section>
</main>
</body>
</html>
```